German Headhunter/ HR Consultancy needs Business Cards Design

We need a business Card Design for our Company in Stuttgart. We are specialized as Headhunter/ HR Consultancy in Placement of specialist and managers in permanent employment. Please refer to our business logo.

```html
<!DOCTYPE html>
<html lang="de">
<head>
<meta charset="utf-8">
<title>Kernwerk Personalberatung – Visitenkarte</title>
<link href="https://fonts.googleapis.com/css2?family=Montserrat:wght@600&family=Arimo:wght@400;700&display=swap" rel="stylesheet">
<style>
  :root {
    --brand-blue: #3a55a7;
    --paper: #ffffff;
    --backdrop: #e9ebee;
    --ink: #1d1d1f;
    --rule-grey: #a9a9ad;
  }
  html, body {
    margin: 0;
    width: 1200px;
    height: 900px;
    overflow: hidden;
    background: var(--backdrop);
  }
  .canvas {
    position: relative;
    width: 1200px;
    height: 900px;
  }
  .card {
    position: absolute;
    left: 300px;
    width: 600px;
    height: 343px;
    box-shadow: 0 6px 18px rgba(0,0,0,0.12);
  }
  .card--front { top: 70px; background: var(--brand-blue); }
  .card--back  { top: 478px; background: var(--paper); }

  /* Front */
  .front-lockup {
    position: absolute;
    left: 110px;
    top: 118px;
    display: flex;
    align-items: center;
    gap: 18px;
  }
  .brand-square {
    width: 92px;
    height: 92px;
    background: var(--paper);
  }
  .front-rules {
    display: flex;
    gap: 10px;
    height: 106px;
  }
  .front-rules span {
    width: 2px;
    height: 100%;
    background: var(--paper);
  }
  .brand-name {
    font-family: "Montserrat", sans-serif;
    font-weight: 600;
    color: var(--paper);
    line-height: 1;
  }
  .brand-name__main {
    display: block;
    font-size: 50px;
    letter-spacing: 1px;
  }
  .brand-name__sub {
    display: block;
    margin-top: 6px;
    font-size: 20px;
    letter-spacing: 1.4px;
  }

  /* Back */
  .back-square {
    position: absolute;
    left: 120px;
    top: 124px;
    width: 104px;
    height: 104px;
    background: var(--brand-blue);
  }
  .back-rules {
    position: absolute;
    left: 258px;
    top: 92px;
    width: 30px;
    height: 170px;
  }
  .contact {
    position: absolute;
    left: 308px;
    top: 82px;
    font-family: "Arimo", sans-serif;
    color: var(--ink);
    font-size: 14px;
    line-height: 1.3;
  }
  .contact__name {
    margin: 0;
    font-weight: 700;
    font-size: 24px;
    color: var(--brand-blue);
    letter-spacing: 0.5px;
    line-height: 1.1;
  }
  .contact__title { margin: 0 0 12px; font-size: 15px; }
  .contact__address { margin: 0 0 12px; font-style: normal; }
  .contact__list { list-style: none; margin: 0; padding: 0; }
  .contact__list li { display: flex; align-items: center; gap: 8px; }
  .contact__list svg { width: 14px; height: 14px; flex: none; }
</style>
</head>
<body>
<main class="canvas">
  <section class="card card--front" aria-label="Vorderseite">
    <div class="front-lockup">
      <div class="brand-square"></div>
      <div class="front-rules"><span></span><span></span></div>
      <div class="brand-name">
        <span class="brand-name__main">KERNWERK</span>
        <span class="brand-name__sub">PERSONALBERATUNG</span>
      </div>
    </div>
  </section>

  <section class="card card--back" aria-label="Rückseite">
    <div class="back-square"></div>
    <svg class="back-rules" viewBox="0 0 30 170" aria-hidden="true">
      <line x1="4" y1="0" x2="4" y2="170" stroke="#3a55a7" stroke-width="1.5"/>
      <line x1="14" y1="18" x2="14" y2="150" stroke="#a9a9ad" stroke-width="1.5"/>
      <line x1="24" y1="28" x2="24" y2="160" stroke="#a9a9ad" stroke-width="1.5"/>
    </svg>
    <div class="contact">
      <h1 class="contact__name">LENA HARTMANN</h1>
      <p class="contact__title">CEO/Founder</p>
      <address class="contact__address">52 Lindenweg<br>Suite 3, Stuttgart 70173</address>
      <ul class="contact__list">
        <li>
          <svg viewBox="0 0 16 16" aria-hidden="true"><path fill="#3a55a7" d="M3 1h3l1.5 4-2 1.2a9 9 0 0 0 4.3 4.3L11 8.5l4 1.5v3a2 2 0 0 1-2 2A12 12 0 0 1 1 3a2 2 0 0 1 2-2z"/></svg>
          (711) 555 - 0182
        </li>
        <li>
          <svg viewBox="0 0 16 16" aria-hidden="true"><rect x="1" y="3" width="14" height="10" fill="#3a55a7"/><path d="M1 3l7 6 7-6" fill="none" stroke="#fff" stroke-width="1.2"/></svg>
          info@kernwerk-personal.com
        </li>
        <li>
          <svg viewBox="0 0 16 16" aria-hidden="true"><circle cx="8" cy="8" r="7" fill="#3a55a7"/><path d="M1 8h14M8 1c-3 3.5-3 10.5 0 14M8 1c3 3.5 3 10.5 0 14" fill="none" stroke="#fff" stroke-width="1"/></svg>
          www.kernwerk-personal.com
        </li>
      </ul>
    </div>
  </section>
</main>
</body>
</html>
```